Business Card Design

We provide services doing multiple jobs in the construction industry.Please note: The company name needs to be ROCK SOLID BUILDING SERVICESAttached logo was an example of what we wanted. Can you change up the colors?

Industry/Entity Type

Construction

Contact Information for Business Card

ROCK SOLID BUILDING SERVICES5401 HUDSON BEND RDAUSTIN, TX 78734(512)243-6854ROCKSOLIDBUILDINGSERVICES@GMAIL.COM

```html
<!DOCTYPE html>
<html lang="en">
<head>
<meta charset="utf-8">
<title>Pearlwood Framing Works – Business Card</title>
<link rel="stylesheet" href="https://fonts.googleapis.com/css2?family=Exo+2:wght@400;500;700&display=swap">
<style>
  :root {
    --backdrop: #e4e6ec;
    --card-white: #f4f4f4;
    --navy-deep: #1b1a55;
    --navy-light: #2b2a7c;
    --stripe: #2a2a2e;
    --text-light: #ffffff;
    --brand-navy: #1f1e62;
  }
  html, body {
    margin: 0;
    width: 1200px;
    height: 840px;
    overflow: hidden;
    background: var(--backdrop);
    font-family: "Exo 2", sans-serif;
  }
  .card {
    position: absolute;
    left: 100px;
    top: 134px;
    width: 1000px;
    height: 572px;
    background: var(--card-white);
    box-shadow: 0 10px 30px rgba(0,0,0,0.18);
    overflow: hidden;
  }
  .card__swoosh {
    position: absolute;
    inset: 0;
    width: 1000px;
    height: 572px;
  }
  .brand {
    position: absolute;
    left: 90px;
    top: 200px;
    display: flex;
    align-items: center;
    gap: 18px;
  }
  .brand__square {
    width: 54px;
    height: 54px;
    background: var(--brand-navy);
  }
  .brand__name {
    margin: 0;
    font-weight: 700;
    font-size: 40px;
    line-height: 1.05;
    letter-spacing: 1px;
    color: var(--brand-navy);
  }
  .contact {
    position: absolute;
    right: 42px;
    top: 58px;
    text-align: right;
    color: var(--text-light);
  }
  .contact__name {
    margin: 0;
    font-weight: 500;
    font-size: 28px;
    letter-spacing: 1.5px;
  }
  .contact__title {
    margin: 2px 0 0;
    font-size: 18px;
    letter-spacing: 1.5px;
  }
  .contact__address {
    margin: 44px 0 40px;
    font-size: 22px;
    line-height: 1.35;
    letter-spacing: 1px;
    font-style: normal;
  }
  .contact__list {
    list-style: none;
    margin: 0;
    padding: 0;
  }
  .contact__item {
    display: flex;
    justify-content: flex-end;
    align-items: center;
    gap: 12px;
    font-size: 21px;
    letter-spacing: 1px;
    height: 36px;
  }
  .contact__item--plain { padding-right: 0; }
  .contact__icon {
    width: 20px;
    height: 20px;
    fill: none;
    stroke: var(--text-light);
    stroke-width: 1.8;
  }
</style>
</head>
<body>
  <div class="card">
    <svg class="card__swoosh" viewBox="0 0 1000 572" aria-hidden="true">
      <defs>
        <linearGradient id="navyFill" x1="0" y1="1" x2="1" y2="0">
          <stop offset="0" stop-color="#1b1a55"/>
          <stop offset="1" stop-color="#2b2a7c"/>
        </linearGradient>
      </defs>
      <path d="M0,488 C340,484 600,318 738,0 L1000,0 L1000,572 L0,572 Z" fill="#2a2a2e"/>
      <path d="M0,502 C352,498 618,330 758,0 L1000,0 L1000,572 L0,572 Z" fill="url(#navyFill)"/>
    </svg>

    <div class="brand">
      <span class="brand__square"></span>
      <p class="brand__name">PEARLWOOD<br>FRAMING WORKS</p>
    </div>

    <div class="contact">
      <p class="contact__name">DELIA HARROWAY</p>
      <p class="contact__title">PRESIDENT</p>
      <address class="contact__address">214, 6th floor, Birchmoor<br>Road TLV</address>
      <ul class="contact__list">
        <li class="contact__item">012 555 0147
          <svg class="contact__icon" viewBox="0 0 20 20"><path d="M4 2h4l1 4-2 1.5a10 10 0 0 0 5.5 5.5L14 11l4 1v4c0 1-1 2-2 2A14 14 0 0 1 2 4c0-1 1-2 2-2z"/></svg>
        </li>
        <li class="contact__item">012 555 0147
          <svg class="contact__icon" viewBox="0 0 20 20"><rect x="5" y="1.5" width="10" height="17" rx="1.5"/><line x1="9" y1="15.5" x2="11" y2="15.5"/></svg>
        </li>
        <li class="contact__item">012 555 0147
          <svg class="contact__icon" viewBox="0 0 20 20"><rect x="2" y="8" width="16" height="10"/><rect x="6" y="2" width="8" height="6"/><line x1="5" y1="12" x2="15" y2="12"/></svg>
        </li>
        <li class="contact__item">yourname@mailnest.example
          <svg class="contact__icon" viewBox="0 0 20 20"><rect x="1.5" y="4" width="17" height="12"/><path d="M1.5 4l8.5 7 8.5-7"/></svg>
        </li>
        <li class="contact__item">www.pearlwoodframing.example
          <svg class="contact__icon" viewBox="0 0 20 20"><circle cx="10" cy="10" r="8.5"/><ellipse cx="10" cy="10" rx="3.8" ry="8.5"/><line x1="1.5" y1="10" x2="18.5" y2="10"/></svg>
        </li>
      </ul>
    </div>
  </div>
</body>
</html>
```